Business card design for holistic health care clinic

We need a double-sided business card design for our holistic health care clinic that integrates our logo design and also its color scheme. My business is called Valmira. It is an integrative medicine clinic. You have already done the logo for me. Please ensure an elegant and upscale design that is not cluttered, but still has all the necessary information (please see below for details).

Target Market(s)

Wellness, fitness, rehabilitation for educated, well-traveled open-minded clients who are focused on natural, organic, balanced and preventive healthcare and lifestyle.

Industry/Entity Type

Medical

Contact Information for Business Card

Modern, clean.

Number of Pages Required

1 page

Font styles to use
Serif
Sans Serif

Colors

Designer to choose colors to be used in the design.

Requirements
Must have
• Logo on one side, all other information on the other side.
• Other information should include:
• Tobias Wrenfeld - DOE, CPT, LMT
• 4100 East Marrow Drive
• Austin, TX 78119
• 512 555 0148
• 818 555 0192
• info@ValmiraHealth.example
• t.wrenfeld@ValmiraHealth.example
Nice to have
• Darker background on front - but not totally black - shaded/dark gray.

```html
<!DOCTYPE html>
<html lang="en">
<head>
<meta charset="utf-8">
<title>Valmira Business Card</title>
<link rel="stylesheet" href="https://fonts.googleapis.com/css2?family=Roboto:wght@400;500&family=Roboto+Condensed:wght@500;700&family=Nunito:wght@700;800&display=swap">
<style>
  :root {
    --backdrop: #5a4a3b;
    --card: #262626;
    --card-light: #2e2e2e;
    --brand-blue: #0a8dc6;
    --text-light: #eaeaea;
  }
  * { margin: 0; padding: 0; box-sizing: border-box; }
  html, body { width: 1200px; height: 960px; overflow: hidden; }
  body { background: var(--backdrop); position: relative; font-family: "Roboto", sans-serif; }

  .card {
    position: absolute;
    width: 600px;
    height: 342px;
    border-radius: 20px;
    background: linear-gradient(180deg, var(--card) 0%, var(--card-light) 100%);
    overflow: hidden;
    box-shadow: 0 3px 6px rgba(0,0,0,0.45);
  }
  .card--front { left: 314px; top: 114px; }
  .card--back { left: 311px; top: 472px; }

  .holder {
    margin-top: 34px;
    text-align: center;
    font-family: "Roboto Condensed", sans-serif;
    color: var(--brand-blue);
  }
  .holder__name { font-size: 22px; font-weight: 700; letter-spacing: 0.2px; }
  .holder__credentials { font-size: 13px; font-weight: 700; }
  .divider {
    width: 30px; height: 2px; background: var(--brand-blue);
    margin: 9px auto 10px;
  }
  .contact { text-align: center; color: var(--text-light); font-size: 14.5px; line-height: 20px; }
  .contact__row { display: flex; justify-content: center; align-items: center; gap: 5px; }
  .contact__item { display: inline-flex; align-items: center; gap: 3px; }
  .icon { width: 12px; height: 12px; fill: var(--brand-blue); }

  .emblem-area {
    position: absolute;
    left: 0; right: 0; bottom: 0;
    height: 150px;
    background: linear-gradient(180deg, rgba(10,141,198,0) 0%, rgba(10,141,198,0.28) 100%);
  }

  .brand {
    position: absolute;
    left: 0; right: 0; top: 142px;
    text-align: center;
    color: var(--brand-blue);
    font-family: "Nunito", sans-serif;
  }
  .brand__name { font-size: 64px; font-weight: 800; line-height: 1; letter-spacing: 1px; }
  .brand__descriptor { font-size: 18px; font-weight: 700; margin-top: 4px; }
  .tagline {
    position: absolute; left: 0; right: 0; top: 282px;
    text-align: center; color: var(--text-light); font-size: 14.5px;
  }
</style>
</head>
<body>
  <section class="card card--front">
    <div class="holder">
      <span class="holder__name">TOBIAS WRENFELD</span>
      <span class="holder__credentials"> - DOE, CPT, LMT</span>
    </div>
    <div class="divider"></div>
    <div class="contact">
      <div class="contact__row">4100 East Marrow Drive, Austin, TX 78119</div>
      <div class="contact__row">
        <span class="contact__item">
          <svg class="icon" viewBox="0 0 24 24"><path d="M6.6 10.8a15 15 0 0 0 6.6 6.6l2.2-2.2c.3-.3.7-.4 1-.2 1.1.4 2.3.6 3.6.6.6 0 1 .4 1 1V20c0 .6-.4 1-1 1A17 17 0 0 1 3 4c0-.6.4-1 1-1h3.5c.6 0 1 .4 1 1 0 1.3.2 2.5.6 3.6.1.3 0 .7-.2 1z"/></svg>512 555 0148
        </span>
        <span class="contact__item">
          <svg class="icon" viewBox="0 0 24 24"><path d="M7 1h10a2 2 0 0 1 2 2v18a2 2 0 0 1-2 2H7a2 2 0 0 1-2-2V3a2 2 0 0 1 2-2zm0 3v14h10V4z"/></svg>818 555 0192
        </span>
        <span class="contact__item">
          <svg class="icon" viewBox="0 0 24 24"><path d="M2 5h20v14H2zm2 2v.5l8 5 8-5V7l-8 5z"/></svg>t.wrenfeld@ValmiraHealth.example
        </span>
      </div>
      <div class="contact__row">
        <span class="contact__item">
          <svg class="icon" viewBox="0 0 24 24"><circle cx="12" cy="12" r="10"/></svg>www.ValmiraHealth.example
        </span>
      </div>
    </div>
    <div class="emblem-area" role="img" aria-label="Large brand emblem decoration in blue"></div>
  </section>

  <section class="card card--back">
    <div class="brand">
      <div class="brand__name">VALMIRA</div>
      <div class="brand__descriptor">Integrative Holistic Medicine</div>
    </div>
    <p class="tagline">it’s all about you – your health, your objectives</p>
  </section>
</body>
</html>
```